Business card for a new cabinet shop company named Veloran Cabinets for high end cabinets

Design a business card, thinking dark rich green with colours to speak of high end luxury ie; cream, gold, black possibly

Mitchell Tarrowby
Director Craftsman
Email: info@veloranjoinery-example.com.au
Instagram : @veloran.cabinets

```html
<!DOCTYPE html>
<html lang="en">
<head>
<meta charset="UTF-8">
<title>Veloran Cabinets — Business Card</title>
<link href="https://fonts.googleapis.com/css2?family=Poppins:wght@300;400;500;600&display=swap" rel="stylesheet">
<style>
  :root {
    --backdrop: #2b2b2f;
    --card: #232528;
    --gold: #c4a564;
    --white: #f2f1ee;
    --rule: #e9e9e9;
  }
  * { margin: 0; padding: 0; box-sizing: border-box; }
  html, body {
    width: 1200px;
    height: 801px;
    overflow: hidden;
    background: var(--backdrop);
    font-family: "Poppins", sans-serif;
  }
  .canvas {
    position: relative;
    width: 1200px;
    height: 801px;
  }
  .card {
    position: absolute;
    top: 257px;
    width: 500px;
    height: 286px;
    background: var(--card);
    overflow: hidden;
    box-shadow: 0 18px 40px rgba(0, 0, 0, 0.45);
  }
  .card--front { left: 50px; }
  .card--back { left: 650px; }

  .brand {
    display: flex;
    align-items: center;
    gap: 12px;
    color: var(--gold);
    font-weight: 500;
    white-space: nowrap;
  }
  .brand__dot {
    width: 14px;
    height: 14px;
    border-radius: 50%;
    background: var(--gold);
    flex: none;
  }
  .card--front .brand {
    position: absolute;
    left: 0;
    right: 0;
    top: 50%;
    transform: translateY(-50%);
    justify-content: center;
    font-size: 34px;
    letter-spacing: 0.5px;
  }

  .card--back .brand {
    position: absolute;
    left: 34px;
    top: 44px;
    font-size: 26px;
  }
  .card__rule {
    position: absolute;
    left: 0;
    top: 0;
  }
  .person {
    position: absolute;
    left: 34px;
    top: 138px;
  }
  .person__name {
    color: var(--white);
    font-weight: 600;
    font-size: 19px;
    line-height: 1.2;
  }
  .person__role {
    color: var(--gold);
    font-weight: 400;
    font-size: 12px;
    letter-spacing: 0.3px;
  }
  .contacts {
    position: absolute;
    left: 34px;
    top: 196px;
    list-style: none;
  }
  .contacts__item {
    display: flex;
    align-items: center;
    gap: 9px;
    color: var(--white);
    font-weight: 300;
    font-size: 11.5px;
    line-height: 19px;
  }
  .contacts__icon {
    width: 11px;
    height: 11px;
    flex: none;
    fill: var(--gold);
  }
  .card__band {
    position: absolute;
    left: 0;
    right: 0;
    bottom: 0;
    height: 7px;
    background: var(--gold);
  }
</style>
</head>
<body>
<main class="canvas">

  <section class="card card--front" aria-label="Card front">
    <div class="brand">
      <span class="brand__dot"></span>
      <span class="brand__name">Veloran Cabinets</span>
    </div>
  </section>

  <section class="card card--back" aria-label="Card back">
    <div class="brand">
      <span class="brand__dot"></span>
      <span class="brand__name">Veloran Cabinets</span>
    </div>

    <svg class="card__rule" width="500" height="286" viewBox="0 0 500 286" aria-hidden="true">
      <line x1="210" y1="162" x2="478" y2="60" stroke="var(--rule)" stroke-width="1"/>
    </svg>

    <div class="person">
      <p class="person__name">Mitchell Tarrowby</p>
      <p class="person__role">Director Craftsman</p>
    </div>

    <ul class="contacts">
      <li class="contacts__item">
        <svg class="contacts__icon" viewBox="0 0 24 24" aria-hidden="true">
          <path d="M6.6 10.8a15.1 15.1 0 0 0 6.6 6.6l2.2-2.2a1 1 0 0 1 1-.25 11.4 11.4 0 0 0 3.6.57 1 1 0 0 1 1 1V20a1 1 0 0 1-1 1A17 17 0 0 1 3 4a1 1 0 0 1 1-1h3.5a1 1 0 0 1 1 1c0 1.25.2 2.45.57 3.57a1 1 0 0 1-.25 1z"/>
        </svg>
        <span>(555) 014-2290</span>
      </li>
      <li class="contacts__item">
        <svg class="contacts__icon" viewBox="0 0 24 24" aria-hidden="true">
          <path d="M2 5h20v14H2z M4 7v.4l8 5.2 8-5.2V7z" fill-rule="evenodd"/>
        </svg>
        <span>info@veloranjoinery-example.com.au</span>
      </li>
      <li class="contacts__item">
        <svg class="contacts__icon" viewBox="0 0 24 24" aria-hidden="true">
          <circle cx="12" cy="12" r="10"/>
        </svg>
        <span>@veloran.cabinets</span>
      </li>
    </ul>

    <div class="card__band"></div>
  </section>

</main>
</body>
</html>
```